Upscale and cool gun range / bar + lounge. Think axe throwing, but much cooler.

capture interest and make them want to know more.

s/b more on the cool and hip side to be on brand

will be offering a gift card. example attached

```html
<!DOCTYPE html>
<html lang="en">
<head>
<meta charset="utf-8">
<title>Brasswick Range Gift Card</title>
<link href="https://fonts.googleapis.com/css2?family=Montserrat:wght@700;800&display=swap" rel="stylesheet">
<style>
  :root {
    --ink: #000000;
    --brass: #f9a51a;
    --paper: #ffffff;
  }
  html, body {
    margin: 0;
    padding: 0;
    overflow: hidden;
    background: var(--ink);
  }
  .gift-card {
    position: relative;
    width: 1200px;
    height: 686px;
    background: var(--ink);
    overflow: hidden;
    font-family: "Montserrat", sans-serif;
  }
  .brand {
    position: absolute;
    left: 68px;
    top: 104px;
    width: 236px;
    display: flex;
    flex-direction: column;
    align-items: center;
    gap: 12px;
  }
  .brand-dot {
    width: 44px;
    height: 44px;
    border: 4px solid var(--brass);
    border-radius: 50%;
    box-sizing: border-box;
  }
  .brand-name {
    margin: 0;
    font-size: 32px;
    font-weight: 700;
    color: var(--brass);
    line-height: 1.08;
    text-align: center;
  }
  .card-value,
  .card-label {
    position: absolute;
    left: 0;
    width: 1200px;
    margin: 0;
    text-align: center;
    line-height: 1;
  }
  .card-value {
    top: 100px;
    padding-left: 8px;
    box-sizing: border-box;
    font-size: 355px;
    font-weight: 800;
    letter-spacing: -0.01em;
    color: var(--brass);
  }
  .card-label {
    top: 446px;
    font-size: 104px;
    font-weight: 800;
    letter-spacing: 0.025em;
    color: var(--paper);
  }
</style>
</head>
<body>
  <main class="gift-card">
    <div class="brand">
      <span class="brand-dot"></span>
      <p class="brand-name">Brasswick<br>Range</p>
    </div>
    <h1 class="card-value">15$</h1>
    <p class="card-label">GIFT CARD</p>
  </main>
</body>
</html>
```